Business Card Design Project

This is the first time we use our new logo. We need a business card that we can use both on our institutional corporate relationships and also that works for our staff that deals with consumers directly.

VELUNDA is a new company dedicated to empower consumers and to provide them with the best choices for specialized health care using the latest telemedicine technology (medicine at a distance via videoconference).

We want to print this cards in high quality materials and process. We will like designs that allow us to use UV spot varnish and other techniques that will differentiate us.

We are including Two different versions of Color logos. In addition we are including white over black background logos. Those can be used replacing the black for a color.

Please note this is the first time we will be creating any corporate materials with our new logo and colors.

Target Market(s)

34+ consumers of medium high and high socioeconomic levels.

Industry/Entity Type

Health

Requirements
Must have
• Our logo on its original colors
Should not have
• Any other graphical element or design that is not our logo

```html
<!DOCTYPE html>
<html lang="en">
<head>
<meta charset="utf-8">
<title>VELUNDA Business Card</title>
<link rel="stylesheet" href="https://fonts.googleapis.com/css2?family=Montserrat:wght@300;400;700;800&family=Arimo:wght@400&display=swap">
<style>
  :root {
    --page-bg: #e9e9ee;
    --card-white: #ffffff;
    --sky-blue: #55b2dd;
    --deep-blue: #1a5a86;
    --brand-blue: #1e74bb;
    --ink: #1c1c1c;
    --rule-grey: #c9c9c9;
  }
  html, body {
    margin: 0;
    padding: 0;
    width: 1200px;
    height: 987px;
    overflow: hidden;
    background: var(--page-bg);
  }
  .sheet {
    width: 1200px;
    height: 987px;
    display: flex;
    flex-direction: column;
    align-items: center;
    justify-content: center;
    gap: 26px;
  }
  .card {
    width: 800px;
    height: 457px;
    border-radius: 26px;
    overflow: hidden;
    box-shadow: 0 3px 10px rgba(0,0,0,0.12);
  }
  .card svg { display: block; }
  .brand-name {
    font-family: "Montserrat", sans-serif;
    font-weight: 800;
    letter-spacing: 2px;
  }
  .holder-name {
    font-family: "Montserrat", sans-serif;
    font-weight: 700;
  }
  .holder-title {
    font-family: "Montserrat", sans-serif;
    font-weight: 300;
  }
  .contact-line, .address-line {
    font-family: "Arimo", Arial, sans-serif;
    fill: var(--ink);
  }
  .web-line {
    font-family: "Montserrat", sans-serif;
    font-weight: 400;
    letter-spacing: 5px;
  }
</style>
</head>
<body>
<main class="sheet">

  <section class="card card-front" aria-label="Card front">
    <svg width="800" height="457" viewBox="0 0 800 457" xmlns="http://www.w3.org/2000/svg">
      <rect class="front-base" width="800" height="457" fill="var(--card-white)"/>
      <path class="front-sky-panel" d="M0,0 H800 V457 H640 C565,250 390,80 0,50 Z" fill="var(--sky-blue)"/>
      <path class="front-curve-stripe" d="M0,50 C390,80 565,250 640,457 H606 C540,262 378,104 0,70 Z" fill="var(--deep-blue)"/>
      <path class="front-thin-arc" d="M0,88 C140,92 225,106 285,126" fill="none" stroke="var(--deep-blue)" stroke-width="2.5"/>

      <g class="brand-lockup">
        <circle cx="50" cy="222" r="17" fill="var(--deep-blue)"/>
        <text class="brand-name" x="78" y="240" font-size="48" fill="var(--deep-blue)">VELUNDA</text>
      </g>

      <g class="holder">
        <text class="holder-name" x="768" y="168" font-size="36" fill="var(--card-white)" text-anchor="end">Your Name</text>
        <text class="holder-title" x="768" y="204" font-size="26" fill="var(--card-white)" text-anchor="end">Title</text>
      </g>

      <g class="contact-list" font-size="17">
        <g class="icon-phone" transform="translate(44,304)">
          <circle r="8" fill="#555"/>
          <path d="M-3,-4 Q-4,2 2,4 L3,2 L1,1 L0,2 Q-2,1 -2,-1 L-1,-2 L-2,-4 Z" fill="#fff"/>
        </g>
        <text class="contact-line" x="60" y="310">012-345-6789</text>
        <g class="icon-phone" transform="translate(44,332)">
          <circle r="8" fill="#555"/>
          <path d="M-3,-4 Q-4,2 2,4 L3,2 L1,1 L0,2 Q-2,1 -2,-1 L-1,-2 L-2,-4 Z" fill="#fff"/>
        </g>
        <text class="contact-line" x="60" y="338">012-345-6789</text>
        <g class="icon-mail" transform="translate(44,360)">
          <circle r="8" fill="#555"/>
          <rect x="-4.5" y="-3" width="9" height="6" fill="#fff"/>
          <path d="M-4.5,-3 L0,0.5 L4.5,-3" fill="none" stroke="#555" stroke-width="1"/>
        </g>
        <text class="contact-line" x="60" y="366">name@velunda.com</text>
        <g class="icon-globe" transform="translate(44,388)">
          <circle r="8" fill="#555"/>
          <circle r="4.5" fill="none" stroke="#fff" stroke-width="1"/>
          <ellipse rx="2" ry="4.5" fill="none" stroke="#fff" stroke-width="1"/>
          <line x1="-4.5" y1="0" x2="4.5" y2="0" stroke="#fff" stroke-width="1"/>
        </g>
        <text class="contact-line" x="60" y="394">www.velunda.com</text>
      </g>

      <line class="contact-divider" x1="236" y1="296" x2="236" y2="404" stroke="var(--rule-grey)" stroke-width="1.5"/>

      <g class="address" font-size="20">
        <text class="address-line" x="256" y="346">Street Name, City Name</text>
        <text class="address-line" x="256" y="374">State, City Zip Code</text>
      </g>
    </svg>
  </section>

  <section class="card card-back" aria-label="Card back">
    <svg width="800" height="457" viewBox="0 0 800 457" xmlns="http://www.w3.org/2000/svg">
      <rect class="back-base" width="800" height="457" fill="var(--brand-blue)"/>
      <g class="brand-lockup">
        <circle cx="238" cy="200" r="26" fill="var(--card-white)"/>
        <text class="brand-name" x="280" y="226" font-size="72" fill="var(--card-white)">VELUNDA</text>
      </g>
      <text class="web-line" x="400" y="300" font-size="22" fill="var(--card-white)" text-anchor="middle">www.velunda.com</text>
    </svg>
  </section>

</main>
</body>
</html>
```